Pinecrest Harbor Foundation Web Design

The design we need is for a WordPress blog that will be our content platform. We are a registered 501(c)3 non-profit that focuses on financially supporting the treatment of cancer patients that have been told they have no hope and there is nothing the conventional medical system can do for them. Through this wesbite we want to both rasie awareness about the treatment options plus, raise funds for treating patients. The two primary target audiences of the site are...

1. Terminally ill patients and their families to let them know that there is an option other then hospice and that we are hear to support that option.

2. People looking to help donate to a worthwhile cause that resonates with them.

The website is https://pinecrestharborfoundation.org/

See attached logo designs!!!

Target Market(s)

Cancer patients and their families

Industry/Entity Type

Foundation

Font styles to use
Sans Serif

Colors
ffffff
fbed22

Requirements
Must have
• I like this look of this site. It is clean, simple, helpful, soft. I like the flow of the pages.
• http://www.meadowsforcalm.org/
• I like the design and flow but NOT the color or boldness
• https://tvbn-youth.org/
• I like this style for a donation page.
• https://www.tumorstudyhub.org/we-are-tsh/join-the-cause/donations/one-time-donation
• with the addition of a Would you like your employer to match? button.
Nice to have
• White black and gold - but soft
• Even possibly grayscale like the site I like.

```html
<!DOCTYPE html>
<html lang="en">
<head>
<meta charset="utf-8">
<title>Pinecrest Harbor Foundation</title>
<link href="https://fonts.googleapis.com/css2?family=Cinzel:wght@400;700&family=Lato:wght@400;700&display=swap" rel="stylesheet">
<style>
:root{
  --gold:#f1cf5c;
  --gold-deep:#e8c24a;
  --ink:#2f2f2f;
  --dark:#333333;
  --card:#595959;
  --muted:#6b6b6b;
  --white:#ffffff;
  --night:#2a3038;
}
*{box-sizing:border-box;margin:0;padding:0}
html,body{width:1200px;height:4235px;overflow:hidden}
body{font-family:'Lato',sans-serif;color:var(--ink);background:var(--white);position:relative}
.abs{position:absolute}
a{color:inherit;text-decoration:none}

/* header */
.topbar{top:0;left:0;width:1200px;height:113px;background:var(--white)}
.brand{left:80px;top:30px;display:flex;align-items:center;gap:12px;font-weight:700;font-size:17px;color:var(--ink);line-height:1.2}
.brand-mark{width:30px;height:30px;background:var(--gold)}
.contact-item{top:40px;display:flex;align-items:center;gap:12px;font-size:16px;color:var(--ink)}
.contact-item .lbl{color:var(--gold-deep)}
.give-btn{left:937px;top:34px;width:187px;height:48px;border:2px solid var(--ink);display:flex;align-items:center;justify-content:center;gap:10px;font-size:16px;color:var(--gold-deep)}

.nav{top:113px;left:0;width:1200px;height:65px;background:var(--gold)}
.nav a{position:absolute;top:22px;font-size:17px;color:var(--ink)}
.search{left:861px;top:12px;width:260px;height:40px;border-radius:20px;background:var(--dark);color:var(--white);font-size:14px;font-style:italic;padding:11px 18px}
.search svg{position:absolute;right:14px;top:11px}

/* hero */
.hero{top:178px;left:0;width:1200px;height:576px;background:linear-gradient(100deg,#4a4744 0%,#8a8079 35%,#b6aba1 55%,#6e655f 80%,#3e3a37 100%)}
.hero-title{width:1200px;text-align:center;font-size:48px;color:var(--white);font-weight:400}
.hero-sub{width:1200px;text-align:center;font-size:16px;color:var(--white)}
.btn{display:flex;align-items:center;justify-content:center;font-size:20px;text-transform:uppercase;letter-spacing:.5px}
.btn-gold{background:var(--gold);color:var(--ink)}
.btn-dark{background:var(--dark);color:var(--white)}

/* about */
.about{top:754px;left:0;width:1200px;height:384px;background:var(--gold)}
.sec-title{font-family:'Cinzel',serif;font-weight:700;font-size:34px;color:var(--ink);text-transform:uppercase}
.sec-title .hl{color:var(--white)}
.about p{position:absolute;left:220px;top:128px;width:790px;text-align:center;color:var(--white);font-size:14px;line-height:24px}

/* services */
.services{top:1138px;left:0;width:1200px;height:474px;background:var(--white)}
.services h2{position:absolute;top:65px;width:1200px;text-align:center;font-family:'Cinzel',serif;font-size:31px;font-weight:700;line-height:42px;color:var(--ink);letter-spacing:1px}
.svc{top:183px;width:228px;height:207px;background:var(--card);padding:10px}
.svc .frame{width:100%;height:100%;border:2px solid var(--white);display:flex;flex-direction:column;align-items:center;padding-top:26px;color:var(--white);text-align:center}
.svc h3{font-weight:400;font-size:24px;margin-top:14px}
.svc p{font-size:13px;line-height:18px;margin-top:8px;width:150px}
.svc.active{background:var(--gold)}
.svc.active .frame{border-color:var(--ink);color:var(--ink)}

/* split panels */
.donate-panel{top:1612px;left:600px;width:600px;height:469px;background:var(--dark)}
.support-panel{top:2081px;left:0;width:600px;height:475px;background:var(--gold)}
.panel-text{position:absolute;font-size:14px;line-height:24px}

/* testimonial */
.testi{top:2556px;left:0;width:1200px;height:319px;background:linear-gradient(90deg,#241f1c,#3a302b 50%,#241f1c)}
.avatar{left:330px;top:2533px;width:128px;height:130px;background:var(--white);padding:6px}
.avatar div{width:100%;height:100%;background:linear-gradient(160deg,#c9a48a,#7a5a48)}
.dots{top:2795px;left:562px;display:flex;gap:8px}
.dots span{width:12px;height:12px;border-radius:50%;border:2px solid var(--white)}
.dots span.on{background:var(--gold);border-color:var(--gold)}

/* blog */
.blog-title{top:2935px;width:1200px;text-align:center}
.post{left:808px;width:320px}
.post h4{font-weight:400;font-size:17px;color:var(--gold-deep)}
.post .date{font-size:12px;color:var(--muted);margin-top:8px}
.post p{font-size:14px;line-height:20px;color:var(--muted);margin-top:6px}
.post .more{font-size:13px;color:var(--gold-deep);margin-top:4px;display:flex;align-items:center;gap:8px}

/* newsletter */
.news{top:3502px;left:0;width:1200px;height:339px;background:var(--gold)}
.field{top:160px;height:44px;border:1px solid var(--ink);display:flex;align-items:center;gap:12px;padding-left:16px;font-size:15px;color:var(--ink)}

/* footer */
.footer{top:3841px;left:0;width:1200px;height:276px;background:linear-gradient(120deg,#3a4450,#242a32 60%,#313a45)}
.contact-card{left:80px;top:3776px;width:632px;height:300px;background:var(--white)}
.ci{position:absolute;top:100px;width:180px;text-align:center;font-size:15px;color:var(--ink)}
.ci .ico{width:60px;height:60px;border-radius:50%;background:var(--gold);margin:0 auto 16px;display:flex;align-items:center;justify-content:center}
.ci .sm{font-size:13px;color:var(--muted);margin-top:20px}
.fcol h5{font-size:19px;font-weight:400;color:var(--gold)}
.fcol li{list-style:none;color:var(--white);font-size:14px;line-height:30px}
.copy{top:4117px;left:0;width:1200px;height:118px;background:#1f242a;border-top:1px solid #4b535c}
.social{top:4154px;display:flex;gap:16px;left:923px}
.social span{width:44px;height:44px;border-radius:50%;background:var(--white)}
.social span:first-child{background:var(--gold)}
</style>
</head>
<body>

<!-- header -->
<header class="abs topbar">
  <div class="abs brand"><span class="brand-mark"></span>Pinecrest Harbor<br>Foundation</div>
  <div class="abs contact-item" style="left:355px">
    <svg width="22" height="22" viewBox="0 0 24 24"><path fill="#2f2f2f" d="M6.6 10.8a15 15 0 006.6 6.6l2.2-2.2a1 1 0 011-.25 11.4 11.4 0 003.6.57 1 1 0 011 1V20a1 1 0 01-1 1A17 17 0 013 4a1 1 0 011-1h3.5a1 1 0 011 1c0 1.25.2 2.45.57 3.6a1 1 0 01-.25 1z"/></svg>
    <span><span class="lbl">Call Us :</span> &nbsp;555-210-0148</span>
  </div>
  <div class="abs contact-item" style="left:592px">
    <svg width="20" height="24" viewBox="0 0 20 24"><path fill="#2f2f2f" d="M10 0a8 8 0 00-8 8c0 6 8 16 8 16s8-10 8-16a8 8 0 00-8-8zm0 11a3 3 0 110-6 3 3 0 010 6z"/></svg>
    <span><span class="lbl">Our Address :</span> &nbsp;214, Harbor Lane, Pinecrest</span>
  </div>
  <a class="abs give-btn" href="#">
    <svg width="20" height="18" viewBox="0 0 24 22"><path fill="none" stroke="#e8c24a" stroke-width="2" d="M12 20S2 14 2 7a5 5 0 0110-1 5 5 0 0110 1c0 7-10 13-10 13z"/></svg>
    Give Donation
  </a>
</header>

<nav class="abs nav">
  <a style="left:80px">Home</a>
  <a style="left:195px">About</a>
  <a style="left:310px">Donate</a>
  <a style="left:440px">Support Hospitality</a>
  <a style="left:666px">News</a>
  <a style="left:780px">Contact</a>
  <div class="abs search">Search here...
    <svg width="18" height="18" viewBox="0 0 20 20"><circle cx="8" cy="8" r="6" fill="none" stroke="#fff" stroke-width="2"/><path d="M12.5 12.5L18 18" stroke="#fff" stroke-width="2"/></svg>
  </div>
</nav>

<!-- hero -->
<section class="abs hero" role="img" aria-label="Photo of two women embracing warmly at home"></section>
<h1 class="abs hero-title" style="top:405px">Fundraising &amp; Charity</h1>
<p class="abs hero-sub" style="top:462px">Your donation is protected. Share your love over a cause.</p>
<a class="abs btn btn-gold" href="#" style="left:508px;top:520px;width:186px;height:60px">Contact Us</a>

<!-- about -->
<section class="abs about">
  <h2 class="abs sec-title" style="top:56px;width:1200px;text-align:center">About <span class="hl">Pinecrest Harbor</span></h2>
  <p>Our foundation helps families facing a hard diagnosis find real treatment options beyond hospice. We fund care, share knowledge and stand beside patients who were told there was nothing left to try. Every gift goes toward treatment, travel and comfort for those who need it most, and every story shared brings new hope to another family.</p>
  <a class="abs btn btn-dark" href="#" style="left:508px;top:262px;width:184px;height:52px;font-size:18px">Read More</a>
</section>

<!-- services -->
<section class="abs services">
  <h2>Everything You Need to Support You in<br>Your Efforts as a Family Caregiver</h2>
  <div class="abs svc" style="left:80px"><div class="frame">
    <svg width="50" height="54" viewBox="0 0 50 54"><circle cx="20" cy="8" r="6" fill="#fff"/><path d="M12 18h14l6 14h10v6H28l-4-8v22h-8V36l-6 16H4l6-20z" fill="#fff"/></svg>
    <h3>Home Care</h3><p>Gentle support for patients at home</p></div></div>
  <div class="abs svc" style="left:351px"><div class="frame">
    <svg width="54" height="54" viewBox="0 0 54 54"><path d="M27 46S6 33 6 18a11 11 0 0121-5 11 11 0 0121 5c0 15-21 28-21 28z" fill="none" stroke="#fff" stroke-width="4"/><path d="M18 22h18" stroke="#fff" stroke-width="4"/></svg>
    <h3>Care Services</h3><p>Help with treatment and daily needs</p></div></div>
  <div class="abs svc active" style="left:622px"><div class="frame">
    <svg width="54" height="54" viewBox="0 0 54 54"><rect x="6" y="16" width="42" height="32" rx="3" fill="#2f2f2f"/><rect x="19" y="8" width="16" height="10" fill="none" stroke="#2f2f2f" stroke-width="4"/><path d="M27 24v16M19 32h16" stroke="#f1cf5c" stroke-width="5"/></svg>
    <h3>Medical Expert</h3><p>Guidance from caring specialists</p></div></div>
  <div class="abs svc" style="left:893px"><div class="frame">
    <svg width="44" height="56" viewBox="0 0 44 56"><path d="M22 4c-8 0-12 6-8 14l16 34 8-6-14-30c2-4 6-6 6-6" fill="none" stroke="#fff" stroke-width="5"/><path d="M22 22L8 52l-8-6 14-28" fill="none" stroke="#fff" stroke-width="5"/></svg>
    <h3>Caregiver job</h3><p>Join the people who give care</p></div></div>
</section>

<!-- donate -->
<div class="abs" style="top:1612px;left:0;width:600px;height:469px;background:linear-gradient(180deg,#d9dde0 0%,#b9bec2 40%,#3c3a3a 70%,#5d4c3e 100%)" role="img" aria-label="Photo of a smiling family standing together in the snow"></div>
<section class="abs donate-panel">
  <h2 class="abs sec-title" style="left:52px;top:62px;font-size:32px;color:var(--gold)">Donate</h2>
  <p class="panel-text" style="left:52px;top:118px;width:490px;color:var(--white)">Your gift helps a patient begin a treatment plan that was once out of reach. Donations cover care costs, travel to clinics and the small comforts that make long days easier. Many donors choose to give monthly, and some ask their employer to match each gift. Whatever you choose, you become part of a circle of people who refuse to give up hope for those who are told there is no way forward.</p>
  <a class="abs btn btn-gold" href="#" style="left:52px;top:351px;width:184px;height:55px;font-size:18px">Read More</a>
</section>

<!-- support -->
<section class="abs support-panel">
  <h2 class="abs sec-title" style="left:80px;top:65px;font-size:32px">Support</h2>
  <p class="panel-text" style="left:80px;top:122px;width:470px;color:var(--ink)">We walk with patients and families through every step, from the first call to the last day of treatment. Our team answers questions, connects families with clinics and helps with paperwork and planning. We listen, we explain options in plain words and we make sure no one feels alone. Reach out at any time and a member of our team will be glad to help you find the next step forward.</p>
  <a class="abs btn btn-dark" href="#" style="left:80px;top:354px;width:182px;height:55px;font-size:18px">Read More</a>
</section>
<div class="abs" style="top:2081px;left:600px;width:600px;height:475px;background:linear-gradient(135deg,#cfd3d6,#a4a7aa 45%,#4d4f55 75%,#e6e6e6)" role="img" aria-label="Photo of a nurse caring for a patient in a treatment chair"></div>

<!-- testimonial -->
<section class="abs testi" role="img" aria-label="Dim background photo of many faces"></section>
<div class="abs avatar" role="img" aria-label="Portrait of the quoted team member"><div></div></div>
<div class="abs" style="left:486px;top:2620px;font-size:19px;color:var(--gold)">Dana Whitfield</div>
<div class="abs" style="left:486px;top:2650px;font-size:13px;color:var(--white)">Manager</div>
<p class="abs" style="left:141px;top:2690px;width:920px;font-size:14px;line-height:24px;color:var(--white)">Working with these families has changed how I see hope. Each week we meet people who were told to stop searching, and each week we help some of them find a path that fits their needs. The kindness of our donors makes that path possible, and we are grateful for every single one of them.</p>
<div class="abs dots"><span></span><span class="on"></span><span></span><span></span></div>

<!-- blog -->
<h2 class="abs sec-title blog-title" style="font-size:34px">Recent <span style="color:var(--gold-deep)">Blog</span></h2>
<div class="abs" style="left:80px;top:3036px;width:363px;height:373px;background:linear-gradient(135deg,#6f7a55,#a49a86 50%,#3f4536)" role="img" aria-label="Photo of a mother in a headscarf with her son"></div>
<svg class="abs" style="left:241px;top:3204px" width="36" height="36" viewBox="0 0 36 36"><circle cx="15" cy="15" r="11" fill="none" stroke="#f1cf5c" stroke-width="3"/><path d="M23 23l10 10M15 10v10M10 15h10" stroke="#f1cf5c" stroke-width="3"/></svg>
<div class="abs" style="left:472px;top:3036px;width:316px;height:164px;background:linear-gradient(135deg,#e4dcd4,#b9372f 40%,#d8d2cc 70%,#8b8580)" role="img" aria-label="Photo of a caregiver with an elderly man"></div>
<div class="abs" style="left:472px;top:3242px;width:316px;height:167px;background:linear-gradient(135deg,#c9a88a,#a82d2a 45%,#e9e4dd 75%,#6d5a4a)" role="img" aria-label="Photo of a family gathered around a grandmother"></div>
<div class="abs post" style="top:3034px">
  <h4>Finding Hope Beyond Hospice</h4>
  <div class="date">Posted at 18/10/2017</div>
  <p>Stories from families who found a new path after being told there was no hope left.</p>
  <div class="more">READ MORE <svg width="26" height="8"><path d="M0 4h24M20 1l4 3-4 3" stroke="#e8c24a" fill="none"/></svg></div>
</div>
<div class="abs post" style="top:3241px">
  <h4>Caring for the Caregiver</h4>
  <div class="date">Posted at 18/10/2017</div>
  <p>How caregivers can rest and stay strong through long months of treatment and care.</p>
  <div class="more">READ MORE <svg width="26" height="8"><path d="M0 4h24M20 1l4 3-4 3" stroke="#e8c24a" fill="none"/></svg></div>
</div>

<!-- newsletter -->
<section class="abs news">
  <p class="abs" style="top:56px;width:1200px;text-align:center;font-size:16px;color:var(--ink)">Want To Stay Up To Date And Receive Downloads Then</p>
  <h2 class="abs" style="top:88px;width:1200px;text-align:center;font-size:31px;font-weight:400;color:var(--ink);letter-spacing:.5px">SUBSCRIBE TO OUR NEWSLETTER</h2>
  <div class="abs field" style="left:141px;width:364px">
    <svg width="18" height="18" viewBox="0 0 20 20"><circle cx="10" cy="6" r="5" fill="#2f2f2f"/><path d="M1 20a9 8 0 0118 0z" fill="#2f2f2f"/></svg>Name :</div>
  <div class="abs field" style="left:517px;width:364px">
    <svg width="20" height="16" viewBox="0 0 20 16"><rect width="20" height="16" rx="2" fill="#2f2f2f"/><path d="M1 2l9 7 9-7" stroke="#f1cf5c" fill="none" stroke-width="1.5"/></svg>Email :</div>
  <a class="abs btn btn-dark" href="#" style="left:892px;top:160px;width:164px;height:44px;font-size:17px">Subscribe</a>
</section>

<!-- footer -->
<footer class="abs footer" role="img" aria-label="Dim background photo of a hospital setting"></footer>
<div class="abs contact-card">
  <h3 class="abs" style="top:28px;width:632px;text-align:center;font-size:22px;font-weight:400">Contact Info</h3>
  <div class="abs" style="left:230px;top:68px;width:172px;height:1px;background:#ccc"></div>
  <div class="ci" style="left:18px">
    <div class="ico"><svg width="26" height="26" viewBox="0 0 24 24"><path fill="#2f2f2f" d="M6.6 10.8a15 15 0 006.6 6.6l2.2-2.2a1 1 0 011-.25 11.4 11.4 0 003.6.57 1 1 0 011 1V20a1 1 0 01-1 1A17 17 0 013 4a1 1 0 011-1h3.5a1 1 0 011 1c0 1.25.2 2.45.57 3.6a1 1 0 01-.25 1z"/></svg></div>
    <div style="margin-top:20px">555-210-0148</div><div class="sm">call us</div></div>
  <div class="ci" style="left:226px">
    <div class="ico"><svg width="22" height="26" viewBox="0 0 20 24"><path fill="#2f2f2f" d="M10 0a8 8 0 00-8 8c0 6 8 16 8 16s8-10 8-16a8 8 0 00-8-8zm0 11a3 3 0 110-6 3 3 0 010 6z"/></svg></div>
    <div>Morgan Ellery<br>CEO</div><div class="sm" style="margin-top:8px">visit us</div></div>
  <div class="ci" style="left:434px">
    <div class="ico"><svg width="26" height="20" viewBox="0 0 20 16"><rect x="1" y="1" width="18" height="14" fill="none" stroke="#2f2f2f" stroke-width="1.6"/><path d="M1 2l9 7 9-7" stroke="#2f2f2f" fill="none" stroke-width="1.6"/></svg></div>
    <div style="margin-top:20px">info@pinecrestharbor.org</div><div class="sm">mail us</div></div>
</div>
<div class="abs fcol" style="left:765px;top:3870px">
  <h5>Useful Link</h5>
  <ul style="margin-top:16px"><li>Home</li><li>About</li><li>Donate</li><li>Support Hospitality</li><li>News</li><li>Contact</li></ul>
</div>
<div class="abs fcol" style="left:951px;top:3870px;width:170px">
  <h5>About Us</h5>
  <div style="margin-top:20px;display:flex;align-items:center;gap:8px;color:var(--white);font-weight:700;font-size:15px"><span style="width:18px;height:18px;background:var(--gold)"></span>Pinecrest Harbor</div>
  <p style="margin-top:14px;color:var(--white);font-size:14px;line-height:20px">Giving hope and real care to patients who were told nothing more could be done.</p>
</div>
<div class="abs copy">
  <p class="abs" style="left:80px;top:48px;font-size:14px;color:var(--white)">copyright | PINECREST HARBOR - 2017. All Right Reserved</p>
</div>
<div class="abs social"><span></span><span></span><span></span><span></span></div>

</body>
</html>
```